Business card for my new company (Accounting firm)

I need a business card for my new business Brightwell Advisory and Ledger SA. Our services are accounting, tax, audit and financial management. Our customers are small companies, start-ups and new companies. The final design has to show financial security, trust and growth. Please find our logo attached to the business card. Text for the business card: Brightwell Advisory and Ledger SA Tomas Varenholt Director and Founder Certified Accountant Tel. 022 418 57 34 tv@clairevalconseil.ch www.clairevalconseil.ch Rue des Vergières 27 1201 Geneva
Target Market(s)
Our customers are small companies, start-ups and new companies.
Industry/Entity Type
Finance And Accounting
Contact Information for Business Card
Claireval Conseil et Comptes SA
Tomas Varenholt
Directeur et Fondateur
Expert-comptable diplômé
Tél. 022 418 57 34
tv@clairevalconseil.ch
www.clairevalconseil.ch
Rue des Vergières 27
1201 Genève

```html
<!DOCTYPE html>
<html lang="fr">
<head>
<meta charset="utf-8">
<title>Claireval Conseil et Comptes SA – Cartes de visite</title>
<link rel="stylesheet" href="https://fonts.googleapis.com/css2?family=Roboto:wght@400;500;700&display=swap">
<style>
  :root {
    --backdrop: #3a3a3d;
    --card: #1d1e22;
    --card-edge: #26272c;
    --blue: #2aa3e0;
    --blue-light: #38b3ee;
    --blue-deep: #0f5d92;
    --white: #ffffff;
    --emboss: #34353b;
  }
  * { margin: 0; padding: 0; box-sizing: border-box; }
  html, body { width: 799px; height: 1200px; overflow: hidden; }
  body {
    background: var(--backdrop);
    font-family: "Roboto", Arial, sans-serif;
    position: relative;
  }
  .card {
    position: absolute;
    left: 80px;
    width: 640px;
    height: 366px;
    background: var(--card);
    border-radius: 4px;
    overflow: hidden;
    box-shadow: 0 18px 30px rgba(0,0,0,0.45);
  }
  .card-front { top: 115px; }
  .card-back { top: 715px; }

  /* Front */
  .front-stripe {
    position: absolute; left: 0; right: 0; bottom: 0;
    height: 12px; background: var(--blue);
  }
  .front-brand {
    position: absolute; left: 0; right: 0; top: 150px;
    text-align: center;
  }
  .front-brand .brand-name {
    display: inline-flex; align-items: center; gap: 12px;
    font-size: 30px; font-weight: 700; letter-spacing: 1px;
    color: var(--emboss);
  }
  .brand-mark { width: 18px; height: 18px; background: currentColor; }

  /* Back */
  .waves { position: absolute; inset: 0; }
  .back-brand {
    position: absolute; left: 34px; top: 112px;
    display: flex; align-items: center; gap: 10px;
    font-size: 25px; font-weight: 700; color: var(--white);
    width: 300px; line-height: 1.15;
  }
  .back-brand .brand-mark { width: 16px; height: 16px; color: var(--blue); flex: none; }
  .identity {
    position: absolute; right: 30px; top: 56px;
    text-align: right; color: var(--white);
  }
  .identity .person { font-size: 20px; font-weight: 700; color: var(--blue); margin-bottom: 4px; }
  .identity .role { font-size: 13.5px; line-height: 1.3; }
  .identity .address { font-size: 13.5px; line-height: 1.3; margin-top: 12px; }
  .contacts {
    position: absolute; right: 30px; top: 268px;
    list-style: none; color: var(--white);
    font-size: 14.5px; text-align: right;
  }
  .contacts li { display: flex; justify-content: flex-end; align-items: center; gap: 10px; height: 22px; }
  .contacts svg { width: 14px; height: 14px; }
</style>
</head>
<body>

<section class="card card-front" aria-label="Recto">
  <div class="front-brand">
    <span class="brand-name"><span class="brand-mark"></span>Claireval Conseil et Comptes</span>
  </div>
  <div class="front-stripe"></div>
</section>

<section class="card card-back" aria-label="Verso">
  <svg class="waves" viewBox="0 0 640 366" preserveAspectRatio="none" aria-hidden="true">
    <defs>
      <linearGradient id="wave-fill" x1="0" y1="0" x2="1" y2="1">
        <stop offset="0" stop-color="#2596d6"/>
        <stop offset="1" stop-color="#0f5d92"/>
      </linearGradient>
    </defs>
    <path d="M0,190 C160,250 400,232 640,205 L640,210 C400,238 160,258 0,198 Z" fill="var(--blue)"/>
    <path d="M0,210 C170,300 420,245 640,200 L640,218 C420,262 170,318 0,232 Z" fill="var(--blue-light)"/>
    <path d="M0,262 C170,330 420,265 640,232 L640,366 L0,366 Z" fill="url(#wave-fill)"/>
  </svg>

  <div class="back-brand"><span class="brand-mark"></span>Claireval Conseil et Comptes</div>

  <div class="identity">
    <p class="person">Tomas Varenholt</p>
    <p class="role">Directeur et Fondateur<br>Expert-comptable diplômé</p>
    <p class="address">Rue des Vergières 27<br>1201 Genève</p>
  </div>

  <ul class="contacts">
    <li>022 418 57 34
      <svg viewBox="0 0 16 16" aria-hidden="true"><path fill="#fff" d="M3 1h3l1 4-2 1a9 9 0 0 0 5 5l1-2 4 1v3c0 1-1 2-2 2C7 15 1 9 1 3c0-1 1-2 2-2z"/></svg>
    </li>
    <li>tv@clairevalconseil.ch
      <svg viewBox="0 0 16 16" aria-hidden="true"><rect x="1" y="3" width="14" height="10" fill="#fff"/><path d="M1 3l7 6 7-6" fill="none" stroke="#1a6fa8" stroke-width="1.3"/></svg>
    </li>
    <li>www.clairevalconseil.ch
      <svg viewBox="0 0 16 16" aria-hidden="true"><circle cx="8" cy="8" r="7" fill="#fff"/><g fill="none" stroke="#1a6fa8" stroke-width="1"><ellipse cx="8" cy="8" rx="3" ry="7"/><path d="M1 8h14M2.5 4.5h11M2.5 11.5h11"/></g></svg>
    </li>
  </ul>
</section>

</body>
</html>
```